ADA COMPLIANCE

We are in need of flyer or tri fold page for ada compliance, handicap ramps and parking lot striping.

Target Market(s)

Commercial Construction Industry

Industry/Entity Type

Parking

Font styles to use
Other font styles liked:
• Felix Titling

Colors
0355a3
acd036

Requirements
Must have
• Our Company Name and logo, 8005172934 number License #2847306
• List of services provided in uploaded images. Navy blue with high vizability green

```html
<!DOCTYPE html>
<html lang="en">
<head>
<meta charset="utf-8">
<title>Summit Ramp Services – Tri-fold Brochure</title>
<link href="https://fonts.googleapis.com/css2?family=Cinzel:wght@400;700&family=Lato:wght@400;700&display=swap" rel="stylesheet">
<style>
  :root {
    --navy: #0355a3;
    --navy-deep: #0b2f8a;
    --ink: #1c2a5c;
    --green: #acd036;
    --green-bright: #c4e842;
    --paper: #ffffff;
    --paper-shade: #eef0f2;
    --text: #222;
    --backdrop: #f6f6f6;
  }
  * { box-sizing: border-box; margin: 0; padding: 0; }
  html, body { width: 1200px; height: 1200px; overflow: hidden; }
  body {
    background: var(--backdrop);
    font-family: "Lato", sans-serif;
    color: var(--text);
    position: relative;
  }
  .brochure {
    position: absolute;
    left: 60px; top: 190px;
    width: 1080px; height: 820px;
    display: flex;
    box-shadow: 0 20px 40px rgba(0,0,0,.12);
  }
  .panel {
    position: relative;
    width: 360px; height: 820px;
    background: linear-gradient(160deg, var(--paper) 0%, var(--paper-shade) 100%);
    overflow: hidden;
  }
  .panel svg.shapes { position: absolute; inset: 0; }
  .body-copy {
    position: absolute;
    font-size: 14.5px;
    line-height: 1.38;
    text-align: justify;
  }
  .pill {
    position: absolute;
    left: 0;
    width: 215px; height: 44px;
    background: var(--green);
    border: 2px solid var(--navy);
    border-left: none;
    border-radius: 0 22px 22px 0;
    font-family: "Cinzel", serif;
    font-weight: 700;
    font-size: 19px;
    color: var(--navy-deep);
    letter-spacing: 1px;
    display: flex; align-items: center;
    padding-left: 44px;
  }
  .contact {
    position: absolute;
    left: 0; right: 0; top: 592px;
    text-align: center;
    font-size: 16px;
    line-height: 1.3;
    color: #222;
  }
  .contact h2 {
    font-family: "Cinzel", serif;
    font-weight: 700;
    font-size: 25px;
    color: var(--ink);
    margin-bottom: 20px;
    display: inline-block;
    border-bottom: 1px solid #bbb;
  }
  .contact p { margin-bottom: 12px; }
  .brand {
    position: absolute;
    top: 150px; left: 0; right: 0;
    text-align: center;
    font-family: "Cinzel", serif;
    font-weight: 400;
    color: var(--ink);
  }
  .brand .name { font-size: 44px; line-height: 1; display: block; }
  .brand .sub { font-size: 13px; letter-spacing: .5px; display: block; border-top: 1px solid var(--ink); margin: 2px 44px 0; }
  .cover-title {
    position: absolute;
    left: 0; right: 0; top: 712px;
    text-align: center;
    font-family: "Cinzel", serif;
    font-weight: 700;
    font-size: 34px;
    color: var(--green-bright);
  }
  .site {
    position: absolute;
    left: 0; right: 0; top: 762px;
    text-align: center;
    font-size: 14px;
    font-weight: 700;
    letter-spacing: 3px;
    color: #fff;
  }
</style>
</head>
<body>
<main class="brochure">

  <!-- Inside panel: services -->
  <section class="panel panel-services">
    <svg class="shapes" viewBox="0 0 360 820" width="360" height="820">
      <path d="M0 170 C40 240 100 270 170 305 C240 340 300 400 360 430 L360 450 C290 420 230 360 160 325 C90 290 30 260 0 200 Z" fill="var(--navy)"/>
      <path role="img" aria-label="Photo of a commercial building with a freshly striped accessible parking lot" d="M0 0 H360 V420 C300 390 240 330 170 300 C100 270 40 240 0 170 Z" fill="url(#lotPhoto)"/>
      <rect x="0" y="794" width="360" height="26" fill="var(--green)"/>
      <defs>
        <linearGradient id="lotPhoto" x1="0" y1="0" x2="0" y2="1">
          <stop offset="0" stop-color="#c9dcef"/>
          <stop offset=".45" stop-color="#c8b9a6"/>
          <stop offset=".6" stop-color="#44484f"/>
          <stop offset="1" stop-color="#2a2d33"/>
        </linearGradient>
      </defs>
    </svg>
    <div class="pill" style="top:404px">Lorem Ipsum</div>
    <p class="body-copy" style="left:44px; width:290px; top:480px">Lorem ipsum dolor sit amet, consectetur adipiscing elit. Maecenas vitae dfvarius libero. Morbi varius enim ultricdffdfes ultrices volutpat. Praesent dfdfdfviverra auctor sagittis. Aliquam erat volutpat.</p>
    <div class="pill" style="top:610px">Lorem Ipsum</div>
    <p class="body-copy" style="left:44px; width:290px; top:684px">Lorem ipsum dolor sit amet, consectetur adipiscing elit. Maecenas vitae dfvarius libero. Morbi varius enim ultricdffdfes ultrices volutpat. Praesent dfdfdfviverra auctor sagittis. Aliquam erat volutpat.</p>
  </section>

  <!-- Back panel: contact -->
  <section class="panel panel-contact">
    <svg class="shapes" viewBox="0 0 360 820" width="360" height="820">
      <defs>
        <linearGradient id="limeWash" x1="0" y1="0" x2="1" y2="1">
          <stop offset="0" stop-color="#b8e03a"/>
          <stop offset="1" stop-color="#9ccc2c"/>
        </linearGradient>
        <linearGradient id="stairPhoto" x1="0" y1="0" x2="0" y2="1">
          <stop offset="0" stop-color="#dfe6ee"/>
          <stop offset=".5" stop-color="#b9b6ae"/>
          <stop offset="1" stop-color="#9a9b9c"/>
        </linearGradient>
      </defs>
      <path d="M0 0 H360 V175 C250 215 150 300 105 545 C80 430 40 360 0 330 Z" fill="url(#limeWash)"/>
      <path d="M360 175 C250 215 150 300 105 545 L112 545 C160 320 260 225 360 195 Z" fill="var(--navy)"/>
      <circle cx="187" cy="305" r="124" fill="var(--navy)"/>
      <circle role="img" aria-label="Photo of a modern building entrance with a concrete stairway and handrails" cx="187" cy="305" r="116" fill="url(#stairPhoto)"/>
      <rect x="0" y="796" width="360" height="24" fill="var(--navy)"/>
    </svg>
    <p class="body-copy" style="left:42px; width:282px; top:44px; font-size:14px">Lorem ipsum dolor sit amet, consectetur adipiscing elit. Maecenas vitae dfvarius libero. Morbi varius enim ultricdffdfes ultrices volutpat. Praesent dfdfdfviverra auctor sagittis. Aliquam erat volutpat.</p>
    <div class="contact">
      <h2>Contact Us</h2>
      <p>Call: , 8005172934</p>
      <p>E-Mail: info@email.com</p>
      <p>Lorem ipsum dolor sit amet<br>45/78/44, lorem street<br>License #2847306</p>
    </div>
  </section>

  <!-- Front cover -->
  <section class="panel panel-cover">
    <svg class="shapes" viewBox="0 0 360 820" width="360" height="820">
      <defs>
        <linearGradient id="coverBlue" x1="0" y1="0" x2="1" y2="1">
          <stop offset="0" stop-color="#0a3ea8"/>
          <stop offset="1" stop-color="var(--navy)"/>
        </linearGradient>
        <linearGradient id="portrait" x1="0" y1="0" x2="0" y2="1">
          <stop offset="0" stop-color="#cfd4da"/>
          <stop offset=".35" stop-color="#9fb8d6"/>
          <stop offset="1" stop-color="#1f2226"/>
        </linearGradient>
      </defs>
      <path d="M0 200 C80 290 220 280 300 340 C340 370 355 440 360 520 L360 560 C340 450 320 390 270 365 C190 325 70 320 0 250 Z" fill="var(--green)"/>
      <rect role="img" aria-label="Photo of a smiling businessman in a dark suit presenting with an open hand" x="120" y="285" width="200" height="400" rx="10" fill="url(#portrait)"/>
      <path d="M0 820 V660 C90 600 240 600 360 520 V820 Z" fill="var(--green)"/>
      <path d="M0 820 V680 C90 620 240 620 360 545 V820 Z" fill="url(#coverBlue)"/>
      <rect x="0" y="796" width="360" height="24" fill="var(--green)"/>
    </svg>
    <div class="brand">
      <span class="name">SUMMIT</span>
      <span class="sub">RAMP SERVICES INC</span>
    </div>
    <div class="cover-title">Lorem Ipsum</div>
    <div class="site">www.website.com</div>
  </section>

</main>
</body>
</html>
```